Hop Bright Meadow Business Website Branding

Looking for a wordpress template design with CSS and HTML encoding. Current website can be seen at hopbrightmeadow.example.

WE ARE CURRENTLY IN PROCESS GETTING A LOGO DESIGN... I HAVE INCLUDED THE TOP POTENTIAL DESIGNS FOR REFERENCE TO HELP UNDERSTAND WHAT STYLE WE ARE LOOKING FOR...
NOTE: THE “PEBBLE CREW” LOGO WAS A PREVIOUS COMPANY WE OWNED SO YOU CAN GE A FEEL FOR THE TYPE OF DESIGNS WE HAVE USED IN THE PAST.

My blog will focus on making a connection with wild Florida, it’s wildlife, plants and animals... with an eye toward Florida conservation, nature adventure trips, and education... Content, photos and other merchandise will also be offered for sale.
I’m looking for a site design that incorporates Florida nature and wildlife/plants, with a fun “Old Florida” retro-adventure feel.
When they see this site it should speak to the import of natural Florida and the critical nature of the ecosystem here... while being instantly recognizable and iconic... IE: when I think of florida I think of water, plants, warmth, sunsets etc...

https://join.chatroomhub.example/t/lumexstudio-kzt4821/shared_invite/zt-pqwrt83m-hRnLvXaKoPzsYcB1Uq7JdM

Target Market(s)

Nature, Education, Conservation, Photography

Industry/Entity Type

Photographer

Coding

Coded - Design and coding required

Requirements
Must have
• Need to have site wide template design which generally includes a landing page and a general page template for other pages... Must include html and css encoding...
Should not have
• Any animals included in the site should be Florida native... IE: no African animals etc... This will require some research to ensure that if animals are included that they are part of the Florida ecosystem.

```html
<!DOCTYPE html>
<html lang="en">
<head>
<meta charset="utf-8">
<title>Hop Bright Meadow</title>
<link href="https://fonts.googleapis.com/css2?family=Domine:wght@400;700&family=Open+Sans:wght@400;600&display=swap" rel="stylesheet">
<style>
:root{
  --cream:#ede2c9;
  --cream-dark:#e3d4b4;
  --red:#8e1414;
  --red-deep:#7a0f10;
  --ink:#1d1b17;
  --white:#ffffff;
  --star:#f3a21c;
}
*{margin:0;padding:0;box-sizing:border-box}
html,body{width:1200px;height:3387px;overflow:hidden}
body{position:relative;background:radial-gradient(ellipse at 30% 40%,#efe5cf 0%,var(--cream) 50%,var(--cream-dark) 100%);font-family:"Open Sans",sans-serif;color:var(--ink)}
.abs{position:absolute}
.serif{font-family:"Domine",serif}
.btn{position:absolute;background:var(--red);color:var(--white);font-family:"Domine",serif;font-weight:700;display:flex;align-items:center;justify-content:center;letter-spacing:.5px}

/* header */
.header{left:0;top:0;width:1200px;height:134px;background:var(--cream)}
.brand{left:89px;top:44px;display:flex;align-items:center;gap:12px;font-family:"Domine",serif;font-weight:700;font-size:27px;color:var(--red)}
.brand-dot{width:34px;height:34px;border-radius:50%;background:var(--red)}
.contact{right:90px;top:18px;display:flex;align-items:center;gap:10px;font-family:"Domine",serif;font-size:18px}
.social{display:flex;gap:12px;margin-left:16px}
.social span{width:24px;height:24px;background:var(--ink);border-radius:3px}
.nav{right:90px;top:80px;display:flex;gap:42px;font-family:"Domine",serif;font-size:17px}
.nav a{color:var(--ink);text-decoration:none}
.nav a.active{color:var(--red)}

/* hero */
.hero{left:0;top:134px;width:1200px;height:590px;background:linear-gradient(180deg,#8d8555 0%,#a8843a 25%,#d07a20 50%,#c7381b 64%,#4a3a3c 76%,#23293a 100%)}
.hero-title{left:0;width:1200px;top:300px;text-align:center;font-family:"Domine",serif;font-weight:700;font-size:58px;color:var(--white)}
.hero-sub{left:0;width:1200px;top:385px;text-align:center;font-size:20.5px;line-height:36px;color:var(--white)}
.hero-curve{left:0;top:620px}

/* about */
.h2{font-family:"Domine",serif;font-weight:700;color:var(--red)}
.about-title{left:89px;top:790px;font-size:41px}
.about-text{left:89px;top:860px;width:445px;font-size:16.5px;line-height:33px;text-align:justify}
.about-photo{left:762px;top:799px;width:349px;height:368px;background:linear-gradient(160deg,#e0a266 0%,#8b7a74 40%,#3aa5c1 75%,#2c6f86 100%)}

/* welcome band */
.welcome{left:0;top:1253px;width:1200px;height:324px;background:linear-gradient(180deg,#2a2620 0%,#141411 60%,#1d1c18 100%)}
.welcome-title{left:0;width:1200px;top:1300px;text-align:center;font-family:"Domine",serif;font-weight:700;font-size:46px;color:var(--white)}
.welcome-text{left:170px;width:860px;top:1372px;text-align:center;font-size:19.5px;line-height:40.5px;color:var(--white)}

/* trips */
.trips-title{left:0;width:1200px;top:1650px;text-align:center;font-size:44px}
.tile{position:absolute;width:329px;height:238px}

/* testimonial */
.testimonial{left:0;top:2425px;width:1200px;height:319px;background:linear-gradient(180deg,#8e1414 0%,#8a1212 70%,#9c2a18 88%,#7a0f10 100%)}
.avatar{left:128px;top:2480px;width:218px;height:218px;border-radius:50%;background:linear-gradient(180deg,#d7d2cc,#8b6a58)}
.stars{left:421px;top:2468px;display:flex;gap:10px}
.quote{left:423px;top:2509px;width:680px;font-size:16.5px;line-height:35px;color:var(--white)}
.quote-name{left:426px;top:2672px;font-family:"Domine",serif;font-weight:700;font-size:24px;color:var(--white);letter-spacing:.5px}
.arrow{top:2552px}

/* blog */
.blog-title{left:0;width:1200px;top:2816px;text-align:center;font-size:44px}
.card{position:absolute;top:2901px;width:330px;height:361px;background:var(--white);border-bottom:6px solid var(--red);box-shadow:0 3px 8px rgba(0,0,0,.18)}
.card-img{height:177px}
.card h3{font-family:"Domine",serif;font-weight:700;font-size:21px;color:var(--red);margin:24px 14px 12px}
.card p{font-size:15px;line-height:29px;margin:0 14px;text-align:justify}

/* footer */
.footer{left:0;top:3309px;width:1200px;height:78px;background:var(--red);color:var(--white);font-family:"Domine",serif;font-size:22px;display:flex;align-items:center;justify-content:center}
</style>
</head>
<body>

<header class="abs header">
  <div class="abs brand"><span class="brand-dot"></span>HOP BRIGHT MEADOW</div>
  <div class="abs contact">
    <svg width="28" height="20" viewBox="0 0 28 20" fill="none" stroke="#1d1b17" stroke-width="2"><rect x="1" y="1" width="26" height="18" rx="2"/><path d="M1 2l13 10 13-10"/></svg>
    <span>Info@MaraFenwick.example</span>
    <div class="social" aria-label="Social links"><span></span><span></span><span></span><span></span></div>
  </div>
  <nav class="abs nav">
    <a class="active" href="#">HOME</a><a href="#">ABOUT US</a><a href="#">ADVENTURE TRIPS</a><a href="#">BLOG</a><a href="#">CONTACT</a>
  </nav>
</header>

<section class="abs hero" role="img" aria-label="Sunset over the Gulf of Mexico"></section>
<svg class="abs hero-curve" width="1200" height="110" viewBox="0 0 1200 110">
  <path d="M0 24 Q600 150 1200 24 L1200 110 L0 110 Z" fill="#ede2c9"/>
  <path d="M0 24 Q600 150 1200 24 L1200 34 Q600 160 0 34 Z" fill="#8e1414"/>
</svg>
<h1 class="abs hero-title">HOP BRIGHT MEADOW</h1>
<p class="abs hero-sub">Come explore wild places and stunning scenery with me as I discover new<br>and exciting eco-adventures and learn about the rare and unique wildlife</p>
<a class="btn" style="left:492px;top:473px;width:216px;height:61px;font-size:22px">GET STARTED</a>

<h2 class="abs h2 about-title">ABOUT ME</h2>
<p class="abs about-text">Hello nature lovers! I’m Mara Fenwick, a wildlife educator, Florida Master Naturalist, nature writer and photographer, busy mama of three kiddos, a playful Havanese puppy, two very chubby guinea pigs, and a giant tree frog. I have a passion for all things nature and I adore living in South-west Florida. I will always be a California girl, but from the moment I set foot in Florida</p>
<a class="btn" style="left:89px;top:1115px;width:175px;height:52px;font-size:19px">READ MORE</a>
<div class="abs about-photo" role="img" aria-label="Portrait photo of the author at the beach"></div>

<section class="abs welcome" role="img" aria-label="Misty Florida pine forest at dusk"></section>
<h2 class="abs welcome-title">WELCOME TO HOP BRIGHT MEADOW</h2>
<p class="abs welcome-text">Come explore wild places and stunning scenery with me as I discover new and exciting eco-adventures and learn about the rare and unique wildlife and environments that make Florida so precious and extraordinary. I hope you can vicariously enjoy the wild and untamed beauty of Florida through my eyes, and learn some amazing things about nature on our explorations.</p>

<h2 class="abs h2 trips-title">NATURE ADVENTURE TRIPS</h2>
<div class="tile" style="left:89px;top:1744px;background:linear-gradient(135deg,#e8445a,#4a5a2c)" role="img" aria-label="Red wildflower petals"></div>
<div class="tile" style="left:435px;top:1744px;background:linear-gradient(135deg,#c9b89a,#3b3a2a)" role="img" aria-label="White peacock butterfly"></div>
<div class="tile" style="left:779px;top:1744px;background:linear-gradient(135deg,#3c6a2e,#a46cc6 55%,#5d7e3a)" role="img" aria-label="Purple blazing star flowers"></div>
<div class="tile" style="left:89px;top:1998px;background:linear-gradient(180deg,#5d6a4e,#b79a4e 55%,#cdb060)" role="img" aria-label="Cattle grazing in a golden prairie"></div>
<div class="tile" style="left:435px;top:1998px;background:linear-gradient(180deg,#4a4a3c,#7a6a56 60%,#5a4a3a)" role="img" aria-label="Florida panther in a forest"></div>
<div class="tile" style="left:779px;top:1998px;background:linear-gradient(160deg,#12335a,#1f4f8a 60%,#4a6d96)" role="img" aria-label="Roseate spoonbill in flight"></div>
<a class="btn" style="left:502px;top:2288px;width:197px;height:53px;font-size:19px">VIEW MORE</a>

<section class="abs testimonial"></section>
<div class="abs avatar" role="img" aria-label="Reviewer portrait"></div>
<div class="abs stars">
  <svg width="26" height="25" viewBox="0 0 24 24"><path fill="#f3a21c" d="M12 1l3.3 7 7.7.8-5.8 5.2 1.7 7.6L12 17.8 5.1 21.6l1.7-7.6L1 8.8 8.7 8z"/></svg>
  <svg width="26" height="25" viewBox="0 0 24 24"><path fill="#f3a21c" d="M12 1l3.3 7 7.7.8-5.8 5.2 1.7 7.6L12 17.8 5.1 21.6l1.7-7.6L1 8.8 8.7 8z"/></svg>
  <svg width="26" height="25" viewBox="0 0 24 24"><path fill="#f3a21c" d="M12 1l3.3 7 7.7.8-5.8 5.2 1.7 7.6L12 17.8 5.1 21.6l1.7-7.6L1 8.8 8.7 8z"/></svg>
  <svg width="26" height="25" viewBox="0 0 24 24"><path fill="#f3a21c" d="M12 1l3.3 7 7.7.8-5.8 5.2 1.7 7.6L12 17.8 5.1 21.6l1.7-7.6L1 8.8 8.7 8z"/></svg>
  <svg width="26" height="25" viewBox="0 0 24 24"><path fill="#f3a21c" d="M12 1l3.3 7 7.7.8-5.8 5.2 1.7 7.6L12 17.8 5.1 21.6l1.7-7.6L1 8.8 8.7 8z"/></svg>
</div>
<p class="abs quote">“Nature has been for me, as long as I remember, a source of solace, inspiration, adventure, and delight; a home, a teacher, a companion.Lorem ipsum dolor sit amet, consectetur adipiscing elit, sed do eiusmod tempor incididunt ut labore et dolore magna aliqua. Ut enim ad minim veniam, quis nostrud exercitation ullamco</p>
<div class="abs quote-name">DELIA HARTWELL</div>
<svg class="abs arrow" style="left:89px" width="12" height="20" viewBox="0 0 12 20"><path d="M10 2L2 10l8 8" fill="none" stroke="#fff" stroke-width="2.5"/></svg>
<svg class="abs arrow" style="left:1100px" width="12" height="20" viewBox="0 0 12 20"><path d="M2 2l8 8-8 8" fill="none" stroke="#fff" stroke-width="2.5"/></svg>

<h2 class="abs h2 blog-title">BLOG</h2>
<article class="card" style="left:89px">
  <div class="card-img" style="background:linear-gradient(180deg,#4f86c9 0%,#cfe0f0 35%,#6a8a3a 55%,#3c5a2c 100%)" role="img" aria-label="Wetland with lily pads and a soaring bird"></div>
  <h3>FINIBUS BONORUM ET</h3>
  <p>Lorem ipsum dolor sit amet, consectetur adipiscing elit, sed do eiusmod tempor incididunt ut labore et dolore</p>
</article>
<article class="card" style="left:438px">
  <div class="card-img" style="background:linear-gradient(180deg,#1f5aa8 0%,#c9dcef 40%,#2c3e58 65%,#3a4a3a 100%)" role="img" aria-label="Open marsh water under a cloudy sky"></div>
  <h3>FINIBUS BONORUM ET</h3>
  <p>Lorem ipsum dolor sit amet, consectetur adipiscing elit, sed do eiusmod tempor incididunt ut labore et dolore</p>
</article>
<article class="card" style="left:783px">
  <div class="card-img" style="background:linear-gradient(180deg,#1e56b0 0%,#9cc0e6 40%,#5a7a32 62%,#b7a255 100%)" role="img" aria-label="Prairie trail leading to a lone tree"></div>
  <h3>FINIBUS BONORUM ET</h3>
  <p>Lorem ipsum dolor sit amet, consectetur adipiscing elit, sed do eiusmod tempor incididunt ut labore et dolore</p>
</article>

<footer class="abs footer">Copyright © 2020 Hop Bright Meadow.</footer>

</body>
</html>
```